-Photo booth rental Web Design Project

Our business is a small photo booth rental service serving the capital region and surrounding areas. The photo booth is a portable booth that fits up to 10 guest. I am looking for a website that will have social media capabilities and also private log ins for clients to view their photo albums online after their event. We provide full service photo booth rentals for all types of parties. I am looking for something fun and unique but also professional and I am also looking to maybe somehow incorporate the age of the photo booth which was invented in 1888. I do not have the photos of our photo booth available because we are just starting up and I wanted to get everything together first but I will provide stock photo booth pictures .Thank you for your patience i know it wont be an easy task with out those things. I added a word document describing information i will need on our website, i am looking for a home page, contact us and book an event page, online gallery page, and pricing. If you need any more information please feel free to contact me. Thanks for your help and I look forward to working with you.

Target Market(s)

For everyone from brides to be for their weddings or private parties, corporate parties, school dances, charity events, community events ect

Industry/Entity Type

Business

Requirements
Nice to have
• social media sharing

```html
<!DOCTYPE html>
<html lang="en">
<head>
<meta charset="utf-8">
<title>FlashLane Photo Booth</title>
<link rel="stylesheet" href="https://fonts.googleapis.com/css2?family=Roboto:wght@400;500;700;900&family=Roboto+Condensed:wght@400;700&display=swap">
<style>
:root{
  --page-bg:#8b7863;
  --paper:#ffffff;
  --ink:#3a3a3a;
  --muted:#777;
  --line:#dcdcdc;
  --tan:#b89a6d;
  --dark:#3b3b3b;
  --brown:#5a3a22;
  --brown-deep:#3e2614;
  --gold:#c9a34f;
  --orange:#e57f2c;
  --slate:#6b7278;
  --blue:#2f8fd0;
  --row-alt:#f2f2f2;
}
*{box-sizing:border-box;margin:0;padding:0}
html,body{width:763px;height:1200px;overflow:hidden}
body{background:var(--page-bg);font-family:"Roboto",sans-serif;color:var(--ink);font-size:9px}
.page{position:absolute;left:36px;top:0;width:694px;height:1172px;background:var(--paper)}
.header{height:68px;display:flex;align-items:center;justify-content:space-between;padding:0 14px}
.brand{display:flex;align-items:center;gap:7px;font-size:18px;font-weight:700;color:var(--brown)}
.brand-dot{width:14px;height:14px;border-radius:50%;background:var(--brown)}
.nav{display:flex;align-items:center;gap:20px;font-size:10px;color:var(--muted)}
.nav .login{background:var(--tan);color:#fff;padding:7px 12px;border-radius:2px}
.hero{position:relative;margin:0 10px;height:338px;overflow:hidden}
.hero-photo{position:absolute;inset:0;background:linear-gradient(110deg,#2c3a2a 0%,#5b6c48 35%,#8a9a70 60%,#4a5a3c 100%)}
.hero-copy{position:absolute;left:400px;top:74px;width:230px;color:#fff}
.hero-copy h1{font-size:22px;font-weight:500;margin-bottom:8px}
.hero-copy p{font-size:9px;line-height:1.45;opacity:.9}
.btn-more{display:inline-block;margin-top:16px;border:1px solid #fff;padding:6px 12px;font-size:8px;letter-spacing:.5px}
.dots{position:absolute;right:20px;bottom:14px;display:flex;gap:5px}
.dots span{width:9px;height:9px;border-radius:50%;background:#fff;opacity:.6}
.dots span:first-child{opacity:1}
.welcome{display:flex;gap:16px;padding:12px 14px;height:124px}
.welcome-text h2{font-size:10px;font-weight:700;margin-bottom:5px}
.welcome-text p{font-size:8.5px;line-height:1.5;color:var(--muted)}
.welcome-photo{flex:0 0 196px;height:96px;background:linear-gradient(135deg,#b7b7b7,#6f6f6f)}
.services{background:var(--dark);height:132px;padding:10px 14px;color:#fff}
.services-head{display:flex;justify-content:space-between;font-size:10px;font-weight:700;letter-spacing:.5px}
.services-list{display:flex;justify-content:space-between;margin-top:18px;padding:0 8px}
.service{width:72px;text-align:center;font-size:7px;font-weight:700;text-transform:uppercase}
.service-icon{width:40px;height:40px;border-radius:50%;background:#fff;margin:0 auto 7px;display:flex;align-items:center;justify-content:center}
.pricing{background:radial-gradient(circle at 40% 40%,var(--brown) 0%,var(--brown-deep) 100%);height:400px;padding:30px 40px;display:flex}
.pricing-intro{width:170px;padding-top:130px;color:#fff}
.pricing-intro h3{font-size:16px;font-family:"Roboto Condensed",sans-serif;font-weight:400;letter-spacing:1px}
.pricing-intro h3 b{font-weight:700}
.pricing-intro small{display:block;font-size:8px;letter-spacing:1px;margin-top:2px}
.deposit{margin-top:26px;background:var(--gold);padding:12px 10px;font-size:8px;line-height:1.5;text-align:center;color:#fff;font-weight:500}
.deposit strong{display:block;font-size:18px;font-weight:700;margin-top:4px}
.tiers{flex:1;display:flex;gap:2px}
.tier{flex:1;background:#fff}
.tier:nth-child(2){background:#f6f6f6}
.tier-head{height:26px;color:#fff;font-weight:700;font-size:9px;letter-spacing:1px;display:flex;align-items:center;justify-content:center;text-transform:uppercase}
.standard .tier-head{background:var(--orange)}
.ultimate .tier-head{background:var(--slate)}
.extreme .tier-head{background:var(--blue)}
.tier ul{list-style:none;padding:6px 8px}
.tier li{font-size:7.5px;padding:5px 0 5px 10px;border-bottom:1px solid var(--line);position:relative;line-height:1.3}
.tier li::before{content:"";position:absolute;left:0;top:8px;width:4px;height:4px;background:var(--muted);border-radius:50%}
.newsletter{display:flex;justify-content:space-between;align-items:center;background:var(--dark);color:#fff;height:40px;padding:0 14px;margin-top:10px;font-size:9px;font-weight:700}
.newsletter input{width:150px;height:16px;border:0;margin-top:3px}
.social{display:flex;gap:4px}
.social span{width:14px;height:14px;background:var(--blue);border-radius:2px}
.footer{text-align:center;font-size:8px;color:var(--muted);padding-top:10px;line-height:1.8}
</style>
</head>
<body>
<div class="page">
  <header class="header">
    <div class="brand"><span class="brand-dot"></span>FlashLane Photo Booth</div>
    <nav class="nav"><span>Home</span><span>Pricing</span><span>Book an Event</span><span>Contact</span><span class="login">Client Login</span></nav>
  </header>

  <section class="hero">
    <div class="hero-photo" role="img" aria-label="Couple posing beside a portable photo booth at an evening event"></div>
    <div class="hero-copy">
      <h1>Photo Booth Rental</h1>
      <p>Capture every laugh of your party with our portable booth, fun props and instant prints your guests will keep for years.</p>
      <span class="btn-more">READ MORE</span>
    </div>
    <div class="dots"><span></span><span></span><span></span></div>
  </section>

  <section class="welcome">
    <div class="welcome-text">
      <h2>WELCOME TO OUR SITE</h2>
      <p>Since the very first photo booth appeared in 1888, people have loved stepping behind the curtain to make memories. We bring that same classic joy to weddings, birthdays, school dances and company events across the capital region. Our booth fits up to ten guests, prints in seconds and shares straight to your favourite social feeds, while private client logins keep your full album safe online after the party.</p>
    </div>
    <div class="welcome-photo" role="img" aria-label="Guests inside the photo booth"></div>
  </section>

  <section class="services">
    <div class="services-head"><span>OUR SERVICES</span><span>‹ ›</span></div>
    <div class="services-list">
      <div class="service"><div class="service-icon"></div>Weddings</div>
      <div class="service"><div class="service-icon"></div>Birthday Parties</div>
      <div class="service"><div class="service-icon"></div>Graduations</div>
      <div class="service"><div class="service-icon"></div>Holiday Parties</div>
      <div class="service"><div class="service-icon"></div>Corporate Parties</div>
      <div class="service"><div class="service-icon"></div>Bridal Showers</div>
      <div class="service"><div class="service-icon"></div>Anniversaries</div>
    </div>
  </section>

  <section class="pricing">
    <div class="pricing-intro">
      <h3><b>PRICING</b> INFORMATION</h3>
      <small>3 TIER PACKAGES</small>
      <div class="deposit">RESERVE YOUR DATE TODAY WITH ANY OF OUR 3 PACKAGES<strong>ONLY $100</strong>deposit</div>
    </div>
    <div class="tiers">
      <div class="tier standard"><div class="tier-head">Standard</div><ul>
        <li>3 hours of service</li><li>Set up &amp; Removal</li><li>Professional &amp; friendly booth attendant</li><li>DVD of full picture gallery</li><li>Guestbook</li><li>Unlimited Prints</li><li>Online Gallery</li><li>Digital Backdrop</li></ul></div>
      <div class="tier ultimate"><div class="tier-head">Ultimate</div><ul>
        <li>4 hours of service</li><li>Set up &amp; Removal</li><li>Professional &amp; friendly booth attendant</li><li>DVD of full picture gallery</li><li>Guestbook</li><li>Unlimited Prints</li><li>Custom Backdrop</li><li>Video Messaging</li><li>Props Package</li><li>Instant Social Media Uploads</li><li>Digital Backdrop</li></ul></div>
      <div class="tier extreme"><div class="tier-head">Extreme</div><ul>
        <li>5 hours of service</li><li>Set up &amp; Removal</li><li>Professional &amp; friendly booth attendant</li><li>DVD of full picture gallery</li><li>Guestbook</li><li>Unlimited Prints</li><li>Video Messaging</li><li>Props Package</li><li>Online Gallery</li><li>Red Carpet Event</li><li>Instant Social Media Uploads</li><li>Digital Backdrop</li></ul></div>
    </div>
  </section>

  <section class="newsletter">
    <div>NEWSLETTER<br><input type="text" aria-label="Email"></div>
    <div>FOLLOW<div class="social"><span></span><span></span><span></span><span></span></div></div>
  </section>

  <footer class="footer">Home | Pricing | Contact Us | Book an Event | Client Log In<br>Copyright 2014 All Rights Reserved</footer>
</div>
</body>
</html>
```